Marlowe Group needs a business card

I would like the card to be simple but modern and elegant.
I like black and white.
or black and gold.
we are a private finance lender and also are involved in property and property developments.

please look at the business card photos i provided i would like M.G only one one side and all the other details on the other side use fonts that tie in with my theme.

Industry/Entity Type

Finance

Contact Information for Business Card

Marlowe Group (M.G) Daniel Marlowe M: 0413586207 E: danmarl@inboxmail.test

Font styles to use
Other font styles liked:
• Use fonts that would reflect our business

Colors
000000
ffffff

Requirements
Must have
• one side of details
• other side has either M.G or Marlowe Group like in the photos provided

```html
<!DOCTYPE html>
<html lang="en">
<head>
<meta charset="utf-8">
<title>Marlowe Group — Business Card</title>
<link rel="stylesheet" href="https://fonts.googleapis.com/css2?family=Michroma&family=Mulish:wght@700&family=Questrial&display=swap">
<style>
  :root {
    --backdrop: #3a322d;
    --card: #121417;
    --ink: #ffffff;
    --ink-soft: #d9dadc;
    --foil: #a9abae;
  }
  * { margin: 0; padding: 0; box-sizing: border-box; }
  html, body { width: 1200px; height: 769px; overflow: hidden; }
  body {
    background: var(--backdrop);
    display: flex;
    align-items: center;
    justify-content: center;
    gap: 60px;
  }
  .card {
    position: relative;
    width: 500px;
    height: 286px;
    background: var(--card);
    border-radius: 3px;
    box-shadow: 0 18px 40px rgba(0,0,0,0.45);
  }
  .monogram {
    position: absolute;
    left: 34px;
    top: 30px;
    font-family: "Michroma", sans-serif;
    font-size: 42px;
    color: var(--ink);
    letter-spacing: 1px;
  }
  .details {
    position: absolute;
    left: 268px;
    top: 168px;
    color: var(--ink-soft);
  }
  .details__name {
    font-family: "Mulish", sans-serif;
    font-weight: 700;
    font-size: 17px;
    color: var(--ink);
    margin-bottom: 6px;
  }
  .details__list { list-style: none; }
  .details__item {
    display: flex;
    align-items: center;
    gap: 8px;
    font-family: "Questrial", sans-serif;
    font-size: 14px;
    line-height: 20px;
  }
  .details__icon { width: 12px; height: 12px; flex: none; fill: var(--ink-soft); }
  .wordmark {
    position: absolute;
    inset: 0;
    display: flex;
    flex-direction: column;
    align-items: center;
    justify-content: center;
    font-family: "Michroma", sans-serif;
    color: var(--foil);
    text-align: center;
  }
  .wordmark__name { font-size: 30px; letter-spacing: 2px; line-height: 1.2; }
  .wordmark__sub { font-size: 15px; letter-spacing: 3px; }
</style>
</head>
<body>
  <section class="card card--front">
    <div class="monogram">M.G</div>
    <div class="details">
      <p class="details__name">Daniel Marlowe</p>
      <ul class="details__list">
        <li class="details__item">
          <svg class="details__icon" viewBox="0 0 12 12" aria-hidden="true"><path d="M3 0h6a1 1 0 0 1 1 1v10a1 1 0 0 1-1 1H3a1 1 0 0 1-1-1V1a1 1 0 0 1 1-1zm0 1.5v8h6v-8z"/></svg>
          0413586207
        </li>
        <li class="details__item">
          <svg class="details__icon" viewBox="0 0 12 12" aria-hidden="true"><path d="M0 2h12v8H0zm1 1v.4l5 3.3 5-3.3V3zm0 1.6V9h10V4.6L6 7.9z"/></svg>
          danmarl@inboxmail.test
        </li>
        <li class="details__item">
          <svg class="details__icon" viewBox="0 0 12 12" aria-hidden="true"><circle cx="6" cy="6" r="6"/></svg>
          www.marlowegroup.test
        </li>
      </ul>
    </div>
  </section>

  <section class="card card--back">
    <div class="wordmark">
      <span class="wordmark__name">MARLOWE</span>
      <span class="wordmark__sub">GROUP (M.G)</span>
    </div>
  </section>
</body>
</html>
```